Marcus & Fiona's Midsummer Unwind Evening

Invitation to a party 60-80 people at a private residence. Age range 30-40s.

Themes: summer/casual/Australian backyard/local community

**For delivery via both email and printed copy**
Would like one document suitable for both purposes or two versions for electronic or paper invitation. I will arrange printing so please prepare it in a suitable format.

Specimen text attached. Address and phone contact to follow by message with successful bidder

Thanks!
Marcus

Target Market(s)

Locals, friends. Party attendees will typicaly be parents in their forties who who be leaving the kids at home for a relaxed party night, and walking home afterward

Industry/Entity Type

Community

Font styles to use
Sans Serif

Requirements
Should not have
• Cliche Australiana imagery. No kangaroos etc

```html
<!DOCTYPE html>
<html lang="en">
<head>
<meta charset="utf-8">
<title>Marcus &amp; Fiona's Midsummer Unwind Evening</title>
<link rel="stylesheet" href="https://fonts.googleapis.com/css2?family=Lato:wght@300;400;700;900&family=Playball&display=swap">
<style>
  :root {
    --plum-top: #6c0a68;
    --magenta: #c8127f;
    --magenta-glow: #f21aa0;
    --violet-deep: #4a0a4c;
    --violet-haze: rgba(150, 30, 170, 0.55);
    --night: #070105;
    --white: #ffffff;
    --script-blush: #ead8e6;
    --ink: #0b0208;
  }
  * { margin: 0; padding: 0; box-sizing: border-box; }
  html, body { width: 857px; height: 1200px; overflow: hidden; background: var(--night); }
  .invitation {
    position: relative;
    width: 857px;
    height: 1200px;
    overflow: hidden;
    font-family: "Lato", sans-serif;
    color: var(--white);
    text-align: center;
    background:
      radial-gradient(ellipse 360px 260px at 50% 40%, rgba(242, 26, 160, 0.55), transparent 70%),
      radial-gradient(ellipse 160px 120px at 10% 64%, var(--violet-haze), transparent 75%),
      radial-gradient(ellipse 160px 120px at 90% 70%, var(--violet-haze), transparent 75%),
      linear-gradient(180deg, var(--plum-top) 0%, var(--magenta) 30%, var(--magenta) 55%, var(--violet-deep) 78%, var(--night) 94%);
  }
  .backdrop-mosaic {
    position: absolute;
    inset: 0;
    background: radial-gradient(ellipse 80% 55% at 50% 35%, rgba(255, 60, 170, 0.18), transparent 75%);
  }
  .line { position: absolute; left: 0; width: 100%; }
  .kicker { top: 44px; font-weight: 700; font-size: 42.5px; }
  .kicker-sub { top: 96px; font-weight: 300; font-size: 42.5px; }
  .hosts { top: 166px; font-weight: 700; font-size: 38px; color: var(--ink); }
  .hosts-rule {
    position: absolute; top: 225px; left: 196px; width: 464px; height: 3px;
    background: linear-gradient(90deg, transparent, var(--ink) 8%, var(--ink) 92%, transparent);
  }
  .event-title {
    position: absolute; top: 268px; left: 0; width: 100%;
    font-family: "Playball", cursive;
    font-weight: 400;
    color: var(--script-blush);
    line-height: 1;
    text-shadow: 0 0 18px rgba(255, 120, 200, 0.35);
  }
  .event-title span { display: block; }
  .title-main { font-size: 120px; }
  .title-second { font-size: 120px; margin-top: -10px; }
  .title-third { font-size: 68px; margin-top: -12px; }
  .audience { top: 612px; font-weight: 700; font-size: 23.5px; }
  .house-silhouette {
    position: absolute; top: 662px; left: 150px; width: 560px; height: 538px;
    background:
      linear-gradient(180deg, rgba(7, 1, 5, 0.55) 0%, rgba(7, 1, 5, 0.92) 22%, var(--night) 45%);
    -webkit-mask-image: linear-gradient(90deg, transparent 0%, #000 10%, #000 90%, transparent 100%);
    mask-image: linear-gradient(90deg, transparent 0%, #000 10%, #000 90%, transparent 100%);
  }
  .when-icon { position: absolute; top: 893px; left: 398px; width: 60px; height: 58px; }
  .date { top: 975px; font-weight: 300; font-size: 28.5px; line-height: 34px; }
  .address { top: 1055px; font-weight: 400; font-size: 26px; line-height: 33px; }
</style>
</head>
<body>
<main class="invitation">
  <div class="backdrop-mosaic" role="img" aria-label="Glowing magenta light-tile backdrop"></div>

  <p class="line kicker">LEAVE THE KIDS AT HOME</p>
  <p class="line kicker-sub">and Let Your Hair Down At</p>
  <p class="line hosts">Marcus &amp; Fiona’s</p>
  <div class="hosts-rule"></div>

  <h1 class="event-title">
    <span class="title-main">Midsummer</span>
    <span class="title-second">Unwind</span>
    <span class="title-third">Evening</span>
  </h1>

  <p class="line audience">For Brindle Heights and friends</p>

  <div class="house-silhouette" role="img" aria-label="Dark silhouette of a house with a chimney"></div>

  <svg class="when-icon" viewBox="0 0 60 58" aria-hidden="true">
    <circle cx="27" cy="27" r="23" fill="none" stroke="#fff" stroke-width="5"/>
    <path d="M27 13 V28 H16" fill="none" stroke="#fff" stroke-width="5" stroke-linecap="round"/>
    <rect x="36" y="34" width="21" height="21" rx="3" fill="#000" stroke="#fff" stroke-width="3"/>
    <g fill="#fff">
      <circle cx="41" cy="42" r="1.6"/><circle cx="46.5" cy="42" r="1.6"/><circle cx="52" cy="42" r="1.6"/>
      <circle cx="41" cy="48" r="1.6"/><circle cx="46.5" cy="48" r="1.6"/><circle cx="52" cy="48" r="1.6"/>
    </g>
  </svg>

  <p class="line date">Saturday 2 January<br>From 6pm ‘til late</p>
  <p class="line address">25 Abcdefg Street,<br>Brindle Heights</p>
</main>
</body>
</html>
```